Business Card Design Project - Brindle Works

We need a new business card that fits with our new logo. We are a social media agency and consultancy operating in China. We want a fresh and strong business card. Our cards need to be two-sided as we have both English and Chinese language names and addresses on the card, but as with our current business card this does not need to be a mirror-image. Our thoughts go out to a white card on the front where the logo/name is and then using the logo colours for different coloured back-grounds. i.e that the back of the biz card works with the four different colours in the logo.

Attached is the new logo, and also a copy of our old business cards.

Target Market(s)

CEO's, CMO's. media and advertising professionals

Industry/Entity Type

Business

Requirements
Must have
• inclusion of both Chinese and English language
Nice to have
• four different colored versions of the back of the biz card. Our logo has four colors and each of these colors we would like to have a version of.

```html
<!DOCTYPE html>
<html lang="en">
<head>
<meta charset="utf-8">
<title>Brindle Works – Business Card</title>
<link rel="stylesheet" href="https://fonts.googleapis.com/css2?family=Open+Sans:wght@400;600&family=Noto+Sans+SC:wght@400;500&display=swap">
<style>
  :root {
    --card-white: #ffffff;
    --brand-green: #8cc63f;
    --ink: #1a1a1a;
    --ink-soft: #3a3a3a;
    --page: #ffffff;
    --shadow: rgba(0, 0, 0, 0.28);
  }
  * { margin: 0; padding: 0; box-sizing: border-box; }
  html, body {
    width: 1200px; height: 629px; overflow: hidden;
    background: var(--page);
    font-family: "Open Sans", "Noto Sans SC", sans-serif;
  }
  .stage { position: relative; width: 1200px; height: 629px; }
  .card {
    position: absolute; top: 160px; width: 514px; height: 312px;
    box-shadow: 4px 8px 14px var(--shadow);
  }
  .card--front { left: 56px; background: var(--card-white); color: var(--ink); }
  .card--back { left: 627px; background: var(--brand-green); color: var(--card-white); }

  .wordmark {
    position: absolute; right: 27px; top: 62px;
    display: flex; align-items: center; gap: 10px;
    font-size: 38px; font-weight: 600; letter-spacing: -0.5px; line-height: 1;
  }
  .wordmark__square { width: 14px; height: 14px; }
  .card--front .wordmark { color: var(--ink); }
  .card--front .wordmark__square { background: var(--brand-green); }
  .card--back .wordmark { color: var(--card-white); }
  .card--back .wordmark__square { background: var(--card-white); }

  .holder { position: absolute; left: 29px; top: 162px; }
  .holder__name { font-size: 30px; font-weight: 400; line-height: 1.05; color: var(--ink); }
  .holder__role { font-size: 15px; color: var(--ink-soft); line-height: 1.2; }

  .contacts {
    position: absolute; left: 29px; top: 238px;
    display: grid; grid-template-columns: 60px auto; row-gap: 1px;
    font-size: 12.5px; line-height: 15px;
  }
  .contacts dt { color: var(--brand-green); font-weight: 600; }
  .contacts dd { color: var(--ink); }

  .web-band {
    position: absolute; left: 278px; right: 0; top: 242px; height: 43px;
    background: var(--brand-green); color: var(--card-white);
    font-size: 20px; line-height: 43px; padding-left: 11px;
  }

  .holder-cn { position: absolute; left: 29px; top: 160px; display: flex; align-items: baseline; gap: 10px; }
  .holder-cn__name { font-family: "Noto Sans SC", sans-serif; font-size: 25px; font-weight: 500; letter-spacing: 2px; }
  .holder-cn__role { font-family: "Noto Sans SC", sans-serif; font-size: 14px; }

  .address { position: absolute; top: 238px; font-size: 12.5px; line-height: 16px; }
  .address--cn { left: 29px; width: 180px; font-family: "Noto Sans SC", sans-serif; }
  .address--en { left: 269px; }
</style>
</head>
<body>
<main class="stage">
  <section class="card card--front" aria-label="Card front">
    <div class="wordmark"><span>Brindle Works</span><span class="wordmark__square"></span></div>
    <div class="holder">
      <p class="holder__name">Owen Castell</p>
      <p class="holder__role">managing director</p>
    </div>
    <dl class="contacts">
      <dt>email:</dt><dd>owen@brindleworks.cn</dd>
      <dt>chat:</dt><dd>owenbeijing</dd>
      <dt>mobile:</dt><dd>+86 13720458817</dd>
    </dl>
    <div class="web-band">www.brindleworks.cn</div>
  </section>

  <section class="card card--back" aria-label="Card back">
    <div class="wordmark"><span>Brindle Works</span><span class="wordmark__square"></span></div>
    <div class="holder-cn" lang="zh">
      <span class="holder-cn__name">柯文德</span>
      <span class="holder-cn__role">董事总经理</span>
    </div>
    <p class="address address--cn" lang="zh">东风广场商务中心套房C310<br>新源北路新源里北路 朝阳<br>区・北京 (100027)</p>
    <p class="address address--en">Dongfeng Plaza Business Centre,<br>Suite C310, Xinyuan North Rd<br>Chaoyang District, Beijing 100027</p>
  </section>
</main>
</body>
</html>
```